Powerpoint template and intro presentation

I have a short presentation of 6 slides that I'd like to be made pretty, see attached below - called target companies Intro.

I'd also like a template incorporating my logo which I have attached below as well

I've attached a jpeg with the logo with white background that is the logo that I would like to incorporate.

Powerpoint and logo file has been uploaded

```html
<!DOCTYPE html>
<html lang="en">
<head>
<meta charset="utf-8">
<title>Table In Green</title>
<link rel="stylesheet" href="https://fonts.googleapis.com/css2?family=Questrial&family=Nunito:wght@700;800&display=swap">
<style>
  :root {
    --backdrop: #ece8e1;
    --slide: #ffffff;
    --brand-green: #7dbe31;
    --rule-green: #c9e1a9;
    --rule-grey: #cfcfcf;
    --title-grey: #555555;
    --cell-text: #5f6a5a;
    --row-dark: #d5e6c7;
    --row-light: #e9f2e0;
  }
  html, body {
    margin: 0;
    width: 1200px;
    height: 1000px;
    overflow: hidden;
    background: var(--backdrop);
  }
  .slide {
    position: absolute;
    left: 33px;
    top: 70px;
    width: 1137px;
    height: 852px;
    background: var(--slide);
    font-family: "Questrial", sans-serif;
  }
  .brand {
    position: absolute;
    left: 50px;
    top: 78px;
    display: flex;
    align-items: center;
    gap: 8px;
  }
  .brand-dot {
    width: 26px;
    height: 26px;
    border-radius: 50%;
    background: var(--brand-green);
    flex: none;
  }
  .brand-name {
    font-size: 18px;
    line-height: 1;
    color: var(--title-grey);
    white-space: nowrap;
  }
  .slide-title {
    position: absolute;
    left: 229px;
    top: 68px;
    margin: 0;
    font-weight: 400;
    font-size: 44px;
    line-height: 1;
    letter-spacing: 2.5px;
    color: var(--title-grey);
  }
  .rule-green, .rule-grey {
    position: absolute;
    height: 0;
  }
  .top-rule.rule-green { left: 229px; right: 0; top: 118px; border-top: 6px solid var(--rule-green); }
  .top-rule.rule-grey  { left: 229px; right: 0; top: 128px; border-top: 2px solid var(--rule-grey); }
  .foot-rule.rule-green { left: 0; width: 1025px; top: 792px; border-top: 6px solid var(--rule-green); }
  .foot-rule.rule-grey  { left: 0; width: 1025px; top: 802px; border-top: 2px solid var(--rule-grey); }
  .page-number {
    position: absolute;
    left: 1038px;
    top: 789px;
    width: 40px;
    height: 40px;
    border-radius: 50%;
    background: var(--brand-green);
    color: #fff;
    font-size: 15px;
    line-height: 40px;
    text-align: center;
  }
  .sales-table {
    position: absolute;
    left: 56px;
    top: 166px;
    width: 1024px;
    border-collapse: separate;
    border-spacing: 2px;
    table-layout: fixed;
  }
  .sales-table th {
    background: var(--brand-green);
    color: #fff;
    font-family: "Nunito", sans-serif;
    font-weight: 800;
    font-size: 26px;
    text-align: left;
    padding: 0 10px;
    height: 43px;
  }
  .sales-table td {
    color: var(--cell-text);
    font-size: 27px;
    line-height: 32px;
    letter-spacing: 0.6px;
    text-align: left;
    vertical-align: top;
    padding: 6px 10px 0;
    height: 38px;
    box-sizing: content-box;
  }
  .sales-table tbody tr:nth-child(odd) td { background: var(--row-dark); }
  .sales-table tbody tr:nth-child(even) td { background: var(--row-light); }
  .sales-table .tall td { height: 61px; }
  .month-note {
    display: block;
    font-size: 20px;
    line-height: 24px;
    letter-spacing: 0.3px;
  }
</style>
</head>
<body>
  <main class="slide">
    <div class="brand">
      <span class="brand-dot"></span>
      <span class="brand-name">Northfield Data</span>
    </div>
    <h1 class="slide-title">Table In Green</h1>
    <div class="top-rule rule-green"></div>
    <div class="top-rule rule-grey"></div>

    <table class="sales-table">
      <thead>
        <tr><th>Month</th><th>Sales Qty</th><th>Sale Cost</th><th>Total Sales</th><th>Profit</th></tr>
      </thead>
      <tbody>
        <tr class="tall"><td>January<span class="month-note">(last quarter)</span></td><td>201</td><td>R 50 900</td><td>R 5600</td><td>R 8 695 224</td></tr>
        <tr><td>February</td><td>201</td><td>R 50 900</td><td>R 5600</td><td>R 8 695 224</td></tr>
        <tr><td>March</td><td>201</td><td>R 50 900</td><td>R 5600</td><td>R 8 695 224</td></tr>
        <tr><td>April</td><td>201</td><td>R 50 900</td><td>R 5600</td><td>R 8 695 224</td></tr>
        <tr><td>May</td><td>201</td><td>R 50 900</td><td>R 5600</td><td>R 8 695 224</td></tr>
        <tr><td>June</td><td>201</td><td>R 50 900</td><td>R 5600</td><td>R 8 695 224</td></tr>
        <tr><td>July</td><td>201</td><td>R 50 900</td><td>R 5600</td><td>R 8 695 224</td></tr>
        <tr><td>August</td><td>201</td><td>R 50 900</td><td>R 5600</td><td>R 8 695 224</td></tr>
        <tr><td>September</td><td>201</td><td>R 50 900</td><td>R 5600</td><td>R 8 695 224</td></tr>
        <tr><td>October</td><td>201</td><td>R 50 900</td><td>R 5600</td><td>R 8 695 224</td></tr>
        <tr><td>November</td><td>201</td><td>R 50 900</td><td>R 5600</td><td>R 8 695 224</td></tr>
      </tbody>
    </table>

    <div class="foot-rule rule-green"></div>
    <div class="foot-rule rule-grey"></div>
    <div class="page-number">14</div>
  </main>
</body>
</html>
```